Property management company looking for modern card design

We at Blue Heron Partners provides property management services for its residential and commercial properties, with expertise in all categories of multifamily, industrial and office projects throughout California.

We need a business card design that is professional and modern designed business card. In our field, clients get hundreds of business cards, we would like our card to stand out.

Please avoid small print.

Target Market(s)

Professionals and high end clients

Industry/Entity Type

Financial Planning

Contact Information for Business Card

Company Name: Blue Heron Partners, Name, email, license #, phone number, website blueheronpartners.com

Font styles to use
Sans Serif

Requirements
Must have
• The card design needs to be adaptable because there is a possibly we will be expanding into different sectors other than real estate. The card design should be focused on financial planning and asset management.
Nice to have
• Modern and simple business card. Eye catching. Non-standard size/shaped cards would be great.
• blueheronpartners.com
Should not have
• Too many bright color or any pictures or shapes of real estate stuff.

```html
<!DOCTYPE html>
<html lang="en">
<head>
<meta charset="utf-8">
<title>Blue Heron Partners – Business Card</title>
<link href="https://fonts.googleapis.com/css2?family=Zilla+Slab:wght@400;500;600&display=swap" rel="stylesheet">
<style>
  :root {
    --backdrop: #4a4a4a;
    --card-dark: #333333;
    --card-kraft: #a98f72;
    --gold: #bca283;
    --ink: #141210;
  }
  * { margin: 0; padding: 0; box-sizing: border-box; }
  html, body {
    width: 1200px;
    height: 1000px;
    overflow: hidden;
    background: var(--backdrop);
    font-family: "Zilla Slab", Georgia, serif;
  }
  .canvas {
    position: relative;
    width: 1200px;
    height: 1000px;
  }
  .card {
    position: absolute;
    left: 287px;
    width: 626px;
    height: 358px;
  }
  .card-front {
    top: 140px;
    background: var(--card-dark);
    display: flex;
    align-items: center;
    justify-content: center;
  }
  .company-name {
    color: var(--gold);
    font-size: 44px;
    font-weight: 500;
    letter-spacing: 0.5px;
    transform: translateY(-2px);
  }
  .card-back {
    top: 531px;
    background: var(--card-kraft);
    color: var(--ink);
    text-align: center;
  }
  .contact-block {
    position: absolute;
    top: 109px;
    left: 0;
    right: 0;
  }
  .person-name {
    font-size: 21px;
    font-weight: 500;
    letter-spacing: 2.4px;
    line-height: 26px;
  }
  .name-rule {
    width: 38px;
    height: 1px;
    background: var(--ink);
    margin: 7px auto 8px;
  }
  .contact-line {
    font-size: 17.5px;
    font-weight: 400;
    letter-spacing: 0.7px;
    line-height: 32px;
  }
  .divider { margin: 0 10px; }
</style>
</head>
<body>
  <main class="canvas">
    <section class="card card-front">
      <h1 class="company-name">Blue Heron Partners</h1>
    </section>
    <section class="card card-back">
      <div class="contact-block">
        <h2 class="person-name">DANIEL MARSH</h2>
        <div class="name-rule"></div>
        <p class="contact-line">License #518406173</p>
        <p class="contact-line">555-0142-3890<span class="divider">|</span>info@blueheronpartners.com</p>
        <p class="contact-line">www.blueheronpartners.com</p>
      </div>
    </section>
  </main>
</body>
</html>
```